Zolvana Stationary and Branding Documents

Corporate Identity Branding stationary needed for IT Recruiting Firm.

I already have a Logo, business cards and website. I need to get designs completed for the remaining corporate identity documents.

The documentation should use similar colors as my website and business card. The designs should modern and clean.

http://zolvanaworks.example/

Target Market(s)

Information Technology Industry

Industry/Entity Type

Information Technology

Colors
3377b5
0255a3
fbee3e
f78f20
f37122
33a6d7
000000
0592cd

Requirements
Must have
• Letter Head
• Folder Design
• PowerPoint Design
• Invoice
• Envelope
Nice to have
• Proposal
• Flyer
• Brochure
Should not have
• Logo
• Business Cards
• Website

```html
<!DOCTYPE html>
<html lang="en">
<head>
<meta charset="utf-8">
<title>Zolvana Letterhead</title>
<link rel="stylesheet" href="https://fonts.googleapis.com/css2?family=Open+Sans:wght@400;700&display=swap">
<style>
  :root {
    --backdrop: #c9d3f2;
    --paper: #f7f8f9;
    --brand-blue: #0255a3;
    --brand-orange: #f37122;
    --ink-grey: #5a5f66;
    --tile-one: #f8ead8;
    --tile-two: #f5e0cc;
    --tile-three: #e6dac8;
  }
  * { margin: 0; padding: 0; box-sizing: border-box; }
  html, body { width: 1200px; height: 784px; overflow: hidden; }
  body {
    background: var(--backdrop);
    font-family: "Open Sans", Arial, sans-serif;
    position: relative;
  }
  .letterhead {
    position: absolute;
    left: 338px;
    top: 22px;
    width: 524px;
    height: 740px;
    background: var(--paper);
    box-shadow: 0 4px 14px rgba(40, 60, 140, 0.25);
    overflow: hidden;
  }
  .corner-bands {
    position: absolute;
    left: 0;
    top: 0;
    width: 524px;
    height: 740px;
  }
  .company-name {
    position: absolute;
    left: 62px;
    top: 92px;
    font-size: 30px;
    font-weight: 700;
    color: var(--brand-blue);
    line-height: 1;
  }
  .contact {
    position: absolute;
    right: 30px;
    top: 150px;
    font-size: 8px;
    line-height: 1.45;
    color: var(--ink-grey);
  }
  .contact-address {
    font-weight: 700;
    color: var(--brand-orange);
  }
  .contact-line {
    display: flex;
    align-items: center;
    gap: 4px;
  }
  .contact-icon {
    width: 6px;
    height: 6px;
    background: var(--brand-blue);
    border-radius: 1px;
    opacity: 0.7;
  }
  .contact-icon.round { border-radius: 50%; }
  .tile {
    position: absolute;
    width: 150px;
    height: 128px;
    border-radius: 18px;
  }
  .tile-one { left: 40px; top: 230px; background: var(--tile-one); }
  .tile-two { left: 170px; top: 350px; background: var(--tile-two); }
  .tile-three { left: 300px; top: 470px; background: var(--tile-three); }
</style>
</head>
<body>
  <main class="letterhead">
    <svg class="corner-bands" viewBox="0 0 524 740" aria-hidden="true">
      <g class="band-top">
        <rect x="0" y="0" width="524" height="14" fill="var(--brand-blue)"/>
        <rect x="0" y="14" width="524" height="4" fill="var(--brand-orange)"/>
      </g>
      <g class="band-bottom">
        <rect x="0" y="722" width="524" height="4" fill="var(--brand-orange)"/>
        <rect x="0" y="726" width="524" height="14" fill="var(--brand-blue)"/>
      </g>
    </svg>

    <div class="company-name">Zolvana</div>

    <div class="contact">
      <div class="contact-address">Two Harbor Plaza 410 Main Street NW</div>
      <div class="contact-line"><span class="contact-icon"></span>8005550142 <span class="contact-icon"></span>info@zolvanaworks.example</div>
      <div class="contact-line"><span class="contact-icon round"></span>www.zolvanaworks.example</div>
    </div>

    <div class="tile tile-one"></div>
    <div class="tile tile-two"></div>
    <div class="tile tile-three"></div>
  </main>
</body>
</html>
```